Marcus Delbridge Finance

Need a personal website advertising Equipment Finance,Business Finance,Commercial Finance, Construction Finance, Bridging Finance. Similar websites are www.corvalend.com.au / www.tarmivest.com.au / www.qbr7.com.au /wwwhalvecredit.com.au

Target Market(s)

Business People

Industry/Entity Type

Business

Number of Pages Required

3 page

Font styles to use
Serif
Sans Serif

Requirements
Must have
• All i want is a simple corporate looking website advertising Equipment Finance, Commercial Finance, Construction Finance, Business Finance, Bridging Finance,

```html
<!DOCTYPE html>
<html lang="en">
<head>
<meta charset="utf-8">
<title>Marcus Delbridge Finance</title>
<link href="https://fonts.googleapis.com/css2?family=Roboto:wght@400;500;700&family=Roboto+Slab:wght@400;700&display=swap" rel="stylesheet">
<style>
:root{
  --blue:#3a7bc8;
  --blue-dark:#2c64a8;
  --blue-deep:#1f5596;
  --ink:#333;
  --muted:#666;
  --line:#d8d8d8;
  --white:#fff;
  --footer-bar:#2e2e2e;
}
*{margin:0;padding:0;box-sizing:border-box}
html,body{width:1200px;height:3203px;overflow:hidden}
body{font-family:"Roboto",Arial,sans-serif;color:var(--ink);background:var(--white);position:relative}
.section{position:absolute;left:0;width:1200px}
.serif{font-family:"Roboto Slab",Georgia,serif}
a{color:inherit;text-decoration:none}

/* header */
.site-header{top:0;height:122px;background:var(--white)}
.brand{position:absolute;left:86px;top:30px;display:flex;align-items:flex-start;gap:14px}
.brand-square{width:30px;height:30px;background:var(--blue);margin-top:8px;flex:none}
.brand-name{font-weight:700;font-size:27px;color:#222;line-height:30px;white-space:nowrap}
.brand-sub{display:block;font-size:20px;font-weight:400;color:var(--blue);line-height:24px}
.top-contact{position:absolute;top:20px;right:86px;display:flex;gap:34px;font-size:13px;color:#444;align-items:center}
.top-contact span{display:flex;align-items:center;gap:10px}
.top-contact b{font-weight:400;color:var(--blue)}
.icon-circle{width:32px;height:32px;border-radius:50%;background:var(--blue);display:flex;align-items:center;justify-content:center}
.main-nav{position:absolute;top:84px;right:86px;display:flex;gap:30px;font-size:13px;color:#333}
.main-nav a.active{color:var(--blue)}

/* hero */
.hero{top:122px;height:523px;background:linear-gradient(90deg,#eef1f4 0%,#f3f4f5 40%,#dfe3e7 100%)}
.hero-photo{position:absolute;left:260px;top:0;width:900px;height:523px;background:radial-gradient(ellipse at 55% 45%,#c9d3de 0%,#dde2e7 45%,rgba(240,242,244,0) 75%)}
.hero-title{position:absolute;left:87px;top:180px;font-size:34px;font-weight:700;color:var(--blue-dark)}
.hero-text{position:absolute;left:87px;top:228px;width:460px;font-size:13px;line-height:22px;color:#444}
.btn-solid{position:absolute;left:87px;top:292px;width:102px;height:36px;background:var(--blue-dark);color:#fff;font-size:12px;border-radius:3px;display:flex;align-items:center;justify-content:center}
.slider-arrow{position:absolute}

/* profile */
.profile{top:645px;height:331px;background:var(--blue);box-shadow:0 14px 18px -10px rgba(0,0,0,.25);z-index:2;color:#fff;text-align:center}
.section-title{font-size:26px;font-weight:400;letter-spacing:.5px}
.profile .section-title{position:absolute;top:52px;width:100%}
.profile-text{position:absolute;top:100px;left:130px;width:940px;font-size:12.5px;line-height:28px}
.profile-actions{position:absolute;top:232px;width:100%;display:flex;justify-content:center;gap:22px}
.btn-outline{border:2px solid #fff;border-radius:3px;height:40px;padding:0 20px;display:flex;align-items:center;font-size:14px;font-weight:500}

/* services / team common */
.services{top:976px;height:536px}
.services .section-title,.team .section-title{position:absolute;top:68px;width:100%;text-align:center;color:var(--blue-dark)}
.card-row{position:absolute;left:86px;top:154px;display:flex;gap:26px}
.card{width:237px;text-align:center}
.card-photo{width:237px;height:234px;position:relative;background:linear-gradient(160deg,#9aa6b4,#5c6f86)}
.card-label{position:absolute;left:0;bottom:0;width:100%;height:44px;background:rgba(58,123,200,.82);color:#fff;font-size:14px;font-weight:500;display:flex;align-items:center;justify-content:center}
.card-text{margin-top:22px;font-size:12.5px;line-height:20px;color:#333;padding:0 12px}
.card-link{margin-top:4px;font-size:11.5px;font-weight:700;color:var(--blue-dark);display:flex;justify-content:center;align-items:center;gap:5px}

/* testimonials */
.testimonials{top:1512px;height:431px;background:linear-gradient(90deg,#3c79c2,#4b88cf 50%,#3c79c2);color:#fff;text-align:center}
.testimonials .section-title{position:absolute;top:64px;width:100%}
.quote-badge{position:absolute;left:510px;top:133px;width:80px;height:80px;border-radius:50%;background:#e9eef4;display:flex;align-items:center;justify-content:center;color:var(--blue);font-size:34px;font-family:"Roboto Slab",serif;font-weight:700}
.client-photo{position:absolute;left:567px;top:123px;width:122px;height:122px;border-radius:50%;background:linear-gradient(160deg,#c8d4e2,#7f95ae);border:4px solid rgba(255,255,255,.6)}
.testimonial-text{position:absolute;top:262px;left:340px;width:520px;font-size:13px;line-height:22px}
.client-name{position:absolute;top:320px;width:100%;font-size:16px;font-weight:500}
.client-role{position:absolute;top:346px;width:100%;font-size:12.5px}

/* team */
.team{top:1943px;height:519px}
.member-photo{width:237px;height:234px;background:linear-gradient(170deg,#b8bec6,#6e7884)}
.member-tag{margin:-38px auto 0;position:relative;width:190px;height:56px;background:#fff;box-shadow:0 1px 4px rgba(0,0,0,.15);padding-top:9px}
.member-tag strong{display:block;font-size:14px;color:#222;font-weight:700}
.member-tag span{font-size:12.5px;color:var(--blue)}
.team .card-link{margin-top:22px;font-weight:500}

/* callback */
.callback{top:2462px;height:446px;background:linear-gradient(90deg,#3a78c4,#4a87ce 60%,#3a78c4);color:#fff}
.callback-title{position:absolute;left:88px;top:98px;font-size:26px}
.callback-rule{position:absolute;left:88px;top:138px;width:330px;height:1px;background:rgba(255,255,255,.7)}
.callback-text{position:absolute;left:88px;top:152px;width:500px;font-size:12px;line-height:20px}
.call-now{position:absolute;left:88px;top:262px;font-size:30px;font-weight:700;letter-spacing:.5px}
.call-now b{margin-left:26px}
.callback-form{position:absolute;left:683px;top:73px;width:427px;height:305px;background:#fff;color:#333;padding:34px 50px 0 50px}
.form-heading{font-size:14px;padding-bottom:12px;border-bottom:1px solid var(--line)}
.form-row{display:flex;gap:30px;margin-top:24px}
.field{flex:1;font-size:13px;padding-bottom:12px;border-bottom:1px solid var(--line)}
.btn-submit{margin:28px auto 0;width:108px;height:44px;background:var(--blue-deep);color:#fff;font-size:14px;font-weight:500;border-radius:3px;display:flex;align-items:center;justify-content:center}

/* footer */
.site-footer{top:2908px;height:248px;background:#fff}
.footer-brand{position:absolute;left:66px;top:60px;text-align:center;width:230px}
.footer-brand .brand-square{margin:0 auto 10px}
.footer-brand .brand-name{font-size:23px}
.footer-col{position:absolute;top:42px}
.footer-col h4{font-size:16px;font-weight:500;color:#333;margin-bottom:18px}
.footer-col li{list-style:none;font-size:12.5px;color:#555;line-height:28px;display:flex;gap:10px;align-items:flex-start}
.footer-col li::before{content:"»";color:#777}
.footer-col.contact li::before{content:none}
.footer-col.contact li{line-height:20px;margin-bottom:10px}
.social{display:flex;gap:8px}
.social span{width:32px;height:32px;border-radius:50%;border:2px solid #666}
.copyright{top:3156px;height:47px;background:var(--footer-bar);color:#ddd;font-size:12px;display:flex;align-items:center;justify-content:center}
</style>
</head>
<body>

<header class="section site-header">
  <div class="brand">
    <div class="brand-square"></div>
    <div class="brand-name">Marcus Delbridge<span class="brand-sub">Finance</span></div>
  </div>
  <div class="top-contact">
    <span><i class="icon-circle"><svg width="16" height="16" viewBox="0 0 24 24"><path fill="#fff" d="M6.6 10.8a15 15 0 0 0 6.6 6.6l2.2-2.2a1 1 0 0 1 1-.25 11.4 11.4 0 0 0 3.6.57 1 1 0 0 1 1 1V20a1 1 0 0 1-1 1A17 17 0 0 1 3 4a1 1 0 0 1 1-1h3.5a1 1 0 0 1 1 1 11.4 11.4 0 0 0 .57 3.6 1 1 0 0 1-.25 1z"/></svg></i>CALL US : <b>617 5550 1820</b></span>
    <span><i class="icon-circle"><svg width="16" height="16" viewBox="0 0 24 24"><rect x="5" y="3" width="14" height="6" fill="#fff"/><rect x="3" y="10" width="18" height="9" rx="2" fill="#fff"/></svg></i>FAX : <b>617 5550 1940</b></span>
  </div>
  <nav class="main-nav">
    <a class="active">HOME</a><a>FINANCE</a><a>KEY PEOPLE</a><a>PRODUCTS</a><a>INVESTORS</a><a>CONTACT US</a>
  </nav>
</header>

<section class="section hero">
  <div class="hero-photo" role="img" aria-label="Smiling finance adviser in shirt and tie seated at a desk with a laptop"></div>
  <h1 class="hero-title serif">MARCUS DELBRIDGE</h1>
  <p class="hero-text">Lorem Ipsum has been the industry's standard dummy text ever since the 1500s, when an unknown printer took a galley.</p>
  <a class="btn-solid">READ MORE</a>
  <svg class="slider-arrow" style="left:34px;top:250px" width="14" height="24"><path d="M12 2 2 12l10 10" fill="none" stroke="#aab" stroke-width="2"/></svg>
  <svg class="slider-arrow" style="right:34px;top:250px" width="14" height="24"><path d="M2 2l10 10L2 22" fill="none" stroke="#aab" stroke-width="2"/></svg>
</section>

<section class="section profile">
  <h2 class="section-title serif">OUR PROFILE</h2>
  <p class="profile-text">Mr. Marcus Delbridge serves as Operations Director of Qarrow Financial Services Pty Ltd. Mr.Delbridge has 16 years experience in the Financial Services and bridging Finance industry, both in Australia, as well as in South Africa. He was employed by the South African based business (BRIGHTVALE FINANCE) for the majority of its operation. He held senior operational positions within Brightvale Finance and provided staff support and direction, training and operational control for the Company. Since the establishment of Qarrow Financial Services bridging loans originated.</p>
  <div class="profile-actions"><a class="btn-outline">READ MORE</a><a class="btn-outline">GET A QUOTE</a></div>
</section>

<section class="section services">
  <h2 class="section-title serif">OUR SERVICES</h2>
  <svg class="slider-arrow" style="left:36px;top:258px" width="14" height="26"><path d="M12 2 2 13l10 11" fill="none" stroke="#9bb8dc" stroke-width="2"/></svg>
  <svg class="slider-arrow" style="right:36px;top:258px" width="14" height="26"><path d="M2 2l10 11L2 24" fill="none" stroke="#9bb8dc" stroke-width="2"/></svg>
  <div class="card-row">
    <div class="card"><div class="card-photo" role="img" aria-label="Hands holding a tablet showing business charts" style="background:linear-gradient(160deg,#3a3f5c,#6a7fa8)"><span class="card-label">EQUIPMENT FINANCE</span></div><p class="card-text">Lorem Ipsum has been the industry's standard dummy text specimen</p><a class="card-link">READ MORE <svg width="11" height="11"><circle cx="5.5" cy="5.5" r="5.5" fill="#2c64a8"/><path d="M4 3l3 2.5L4 8" stroke="#fff" fill="none" stroke-width="1.5"/></svg></a></div>
    <div class="card"><div class="card-photo" role="img" aria-label="Business team meeting around a table" style="background:linear-gradient(160deg,#d9c7b3,#8a7563)"><span class="card-label">BUSINESS FINANCE</span></div><p class="card-text">Lorem Ipsum has been the industry's standard dummy text specimen</p><a class="card-link">READ MORE <svg width="11" height="11"><circle cx="5.5" cy="5.5" r="5.5" fill="#2c64a8"/><path d="M4 3l3 2.5L4 8" stroke="#fff" fill="none" stroke-width="1.5"/></svg></a></div>
    <div class="card"><div class="card-photo" role="img" aria-label="Colleagues working together at a laptop in an office" style="background:linear-gradient(160deg,#e3ddd6,#8d8a88)"><span class="card-label">COMMERCIAL FINANCE</span></div><p class="card-text">Lorem Ipsum has been the industry's standard dummy text specimen</p><a class="card-link">READ MORE <svg width="11" height="11"><circle cx="5.5" cy="5.5" r="5.5" fill="#2c64a8"/><path d="M4 3l3 2.5L4 8" stroke="#fff" fill="none" stroke-width="1.5"/></svg></a></div>
    <div class="card"><div class="card-photo" role="img" aria-label="Construction workers in hard hats in a warehouse" style="background:linear-gradient(160deg,#c9a66a,#6f6a63)"><span class="card-label">CONSTRUCTION FINANCE</span></div><p class="card-text">Lorem Ipsum has been the industry's standard dummy text specimen</p><a class="card-link">READ MORE <svg width="11" height="11"><circle cx="5.5" cy="5.5" r="5.5" fill="#2c64a8"/><path d="M4 3l3 2.5L4 8" stroke="#fff" fill="none" stroke-width="1.5"/></svg></a></div>
  </div>
</section>

<section class="section testimonials">
  <h2 class="section-title serif">CLIENT TESTIMONIALS</h2>
  <svg class="slider-arrow" style="left:305px;top:200px" width="14" height="26"><path d="M12 2 2 13l10 11" fill="none" stroke="#c6d8ef" stroke-width="2"/></svg>
  <svg class="slider-arrow" style="right:305px;top:200px" width="14" height="26"><path d="M2 2l10 11L2 24" fill="none" stroke="#c6d8ef" stroke-width="2"/></svg>
  <div class="quote-badge">“</div>
  <div class="client-photo" role="img" aria-label="Portrait of the client"></div>
  <p class="testimonial-text">Lorem Ipsum passages, and more recently with desktop publishing software like Quillset Layout including versions of Lorem Ipsum</p>
  <p class="client-name">DEVRAN SOLTE</p>
  <p class="client-role">Client</p>
</section>

<section class="section team">
  <h2 class="section-title serif">OUR EXPERT TEAM</h2>
  <svg class="slider-arrow" style="left:36px;top:258px" width="14" height="26"><path d="M12 2 2 13l10 11" fill="none" stroke="#9bb8dc" stroke-width="2"/></svg>
  <svg class="slider-arrow" style="right:36px;top:258px" width="14" height="26"><path d="M2 2l10 11L2 24" fill="none" stroke="#9bb8dc" stroke-width="2"/></svg>
  <div class="card-row">
    <div class="card"><div class="member-photo" role="img" aria-label="Portrait of team member" style="background:linear-gradient(170deg,#a9c4e4,#4f7fb6)"></div><div class="member-tag"><strong>MS. LENA ORVIK</strong><span>Manager</span></div><a class="card-link">View Details <svg width="11" height="11"><circle cx="5.5" cy="5.5" r="5.5" fill="#2c64a8"/><path d="M4 3l3 2.5L4 8" stroke="#fff" fill="none" stroke-width="1.5"/></svg></a></div>
    <div class="card"><div class="member-photo" role="img" aria-label="Portrait of team member"></div><div class="member-tag"><strong>MS. LENA ORVIK</strong><span>Manager</span></div><a class="card-link">View Details <svg width="11" height="11"><circle cx="5.5" cy="5.5" r="5.5" fill="#2c64a8"/><path d="M4 3l3 2.5L4 8" stroke="#fff" fill="none" stroke-width="1.5"/></svg></a></div>
    <div class="card"><div class="member-photo" role="img" aria-label="Portrait of team member" style="background:linear-gradient(170deg,#c7c3bd,#7b7670)"></div><div class="member-tag"><strong>MS. LENA ORVIK</strong><span>Manager</span></div><a class="card-link">View Details <svg width="11" height="11"><circle cx="5.5" cy="5.5" r="5.5" fill="#2c64a8"/><path d="M4 3l3 2.5L4 8" stroke="#fff" fill="none" stroke-width="1.5"/></svg></a></div>
    <div class="card"><div class="member-photo" role="img" aria-label="Portrait of team member" style="background:linear-gradient(170deg,#9ea3a8,#4e5358)"></div><div class="member-tag"><strong>MS. LENA ORVIK</strong><span>Manager</span></div><a class="card-link">View Details <svg width="11" height="11"><circle cx="5.5" cy="5.5" r="5.5" fill="#2c64a8"/><path d="M4 3l3 2.5L4 8" stroke="#fff" fill="none" stroke-width="1.5"/></svg></a></div>
  </div>
</section>

<section class="section callback" role="img" aria-label="Faint blue-tinted background of a businessman on the phone">
  <h2 class="callback-title serif">REQUEST FOR CALL BACK</h2>
  <div class="callback-rule"></div>
  <p class="callback-text">Lorem Ipsum passage, and going through the cites of the word in classical literature, discovered the undoubtable source. Lorem Ipsum comes from sections 1.10.32 and 1.10.33 of "de Finibus Bonorum et Malorum"The first line of Lorem Ipsum, "Lorem ipsum dolor sit amet..", comes from a line in section 1.10.32.</p>
  <p class="call-now">CALL NOW ! ! <b>617 5550 1820</b></p>
  <form class="callback-form">
    <p class="form-heading">Discussions With Financial Experts*</p>
    <div class="form-row"><span class="field">First Name</span><span class="field">Last Name</span></div>
    <div class="form-row"><span class="field">Enter Mail *</span><span class="field">Phone *</span></div>
    <a class="btn-submit">SUBMIT</a>
  </form>
</section>

<footer class="section site-footer">
  <div class="footer-brand">
    <div class="brand-square"></div>
    <div class="brand-name">Marcus Delbridge<span class="brand-sub">Finance</span></div>
  </div>
  <div class="footer-col" style="left:320px"><h4>QUICK LINKS</h4><ul><li>Home</li><li>Finance</li><li>Key Product</li><li>Blog</li><li>Contact us</li></ul></div>
  <div class="footer-col" style="left:488px"><h4>SERVICES</h4><ul><li>Equipment Finance</li><li>Business Finance</li><li>Commercial Finance</li><li>Construction Finance</li><li>Bridging Finance</li></ul></div>
  <div class="footer-col contact" style="left:700px"><h4>CONTACT US</h4><ul>
    <li><svg width="14" height="14" viewBox="0 0 24 24"><path fill="#666" d="M12 3 2 12h3v9h5v-6h4v6h5v-9h3z"/></svg><span>14 Harbour Lane<br>Coral Bay, Queensland<br>4870 Australia</span></li>
    <li><svg width="14" height="14" viewBox="0 0 24 24"><path fill="#666" d="M6.6 10.8a15 15 0 0 0 6.6 6.6l2.2-2.2a1 1 0 0 1 1-.25 11.4 11.4 0 0 0 3.6.57 1 1 0 0 1 1 1V20a1 1 0 0 1-1 1A17 17 0 0 1 3 4a1 1 0 0 1 1-1h3.5a1 1 0 0 1 1 1 11.4 11.4 0 0 0 .57 3.6 1 1 0 0 1-.25 1z"/></svg><span>Call Us : (913)555-0142</span></li>
    <li><svg width="14" height="14" viewBox="0 0 24 24"><rect x="2" y="5" width="20" height="14" fill="#666"/><path d="M2 5l10 8 10-8" stroke="#fff" fill="none" stroke-width="1.5"/></svg><span>info@delbridgefinance.example</span></li>
  </ul></div>
  <div class="footer-col" style="left:945px"><h4>FOLLOW US</h4><div class="social"><span></span><span></span><span></span><span></span></div></div>
</footer>

<div class="section copyright">@copyright 2017 Marcus Delbridge . All Rights Reserved</div>

</body>
</html>
```